KiteMarvel "The Gift that keeps on Styling"

Please be creative in design. We are a fashion company that sends monthly boxes to women all over the US our company is called GarbNest. We want to launch a holiday marketing campaign that says:

KiteMarvel ( please use empire font for this )

The gift that keeps on styling

See attached images that can be utilized for graphic. This is for our holiday promos, advertising and campaigns.

Please use many images of provided.

Target Market(s)

All holiday buyer that are gifting women.

Industry/Entity Type

Advertising

Requirements
Must have
• 2 different layouts required Facebook banner Post Card size 4X6

Should not have
• Only just one image please use more than one image.

```html
<!DOCTYPE html>
<html lang="en">
<head>
<meta charset="utf-8">
<title>KiteMarvel Holiday Postcard</title>
<link rel="stylesheet" href="https://fonts.googleapis.com/css2?family=Antonio:wght@300;400&family=Oswald:wght@400&display=swap">
<style>
  :root {
    --stage: #2a211c;
    --card-top: #ea5883;
    --card-mid: #d63c63;
    --card-bottom: #b51f3e;
    --pattern: #f27a9d;
    --ink: #0d0b0c;
    --gold-light: #fff2a8;
    --gold: #e0b240;
    --gold-deep: #a86d14;
    --pill-text: #3a2208;
    --photo-skin: #d9a98e;
    --photo-dress: #1c1618;
    --photo-soft: #e88aa6;
    --ornament: #f07b9c;
  }
  * { margin: 0; padding: 0; box-sizing: border-box; }
  html, body {
    width: 1200px;
    height: 840px;
    overflow: hidden;
    background: var(--stage);
  }
  .postcard {
    position: absolute;
    left: 30px;
    top: 42px;
    width: 1140px;
    height: 756px;
    overflow: hidden;
    background: linear-gradient(180deg, var(--card-top) 0%, var(--card-mid) 45%, var(--card-bottom) 100%);
  }
  .pattern-area {
    position: absolute;
    inset: 0;
    background: radial-gradient(ellipse at 50% 20%, var(--pattern) 0%, rgba(242,122,157,0) 65%);
    opacity: 0.35;
  }
  .ornament-area {
    position: absolute;
    left: 800px;
    top: 486px;
    width: 340px;
    height: 270px;
    background: radial-gradient(ellipse at 70% 55%, var(--ornament) 0%, rgba(240,123,156,0) 70%);
    opacity: 0.7;
  }
  .accent-photo {
    position: absolute;
    left: 960px;
    top: 40px;
    width: 170px;
    height: 300px;
    border-radius: 85px;
    background: linear-gradient(180deg, var(--photo-soft) 0%, var(--card-mid) 100%);
    opacity: 0.55;
  }
  .model-photo {
    position: absolute;
    left: 811px;
    top: 22px;
    width: 262px;
    height: 726px;
    border-radius: 120px 120px 40px 40px;
    background: linear-gradient(180deg, var(--photo-skin) 0%, var(--photo-dress) 22%, var(--photo-dress) 52%, var(--photo-skin) 66%, var(--photo-skin) 100%);
    opacity: 0.9;
  }
  .headline {
    position: absolute;
    left: 50px;
    top: 232px;
    font-family: "Antonio", sans-serif;
    font-weight: 300;
    font-size: 139px;
    line-height: 1;
    letter-spacing: 12px;
    text-transform: uppercase;
    white-space: nowrap;
  }
  .headline .word-dark { color: var(--ink); }
  .headline .word-gold {
    background: linear-gradient(180deg, var(--gold-light) 0%, var(--gold) 45%, var(--gold-deep) 100%);
    -webkit-background-clip: text;
    background-clip: text;
    color: transparent;
  }
  .gold-rule {
    position: absolute;
    left: 52px;
    top: 419px;
    width: 1088px;
    height: 4px;
    background: linear-gradient(90deg, var(--gold-deep), var(--gold-light) 40%, var(--gold) 100%);
  }
  .tagline-pill {
    position: absolute;
    left: 52px;
    top: 454px;
    width: 696px;
    height: 49px;
    border-radius: 10px;
    background: linear-gradient(180deg, var(--gold-light) 0%, var(--gold) 45%, var(--gold-deep) 100%);
    box-shadow: 0 2px 4px rgba(0,0,0,0.35);
    display: flex;
    align-items: center;
    justify-content: center;
    font-family: "Oswald", sans-serif;
    font-size: 20px;
    letter-spacing: 7px;
    color: var(--pill-text);
    text-transform: uppercase;
    white-space: nowrap;
  }
</style>
</head>
<body>
  <main class="postcard">
    <div class="pattern-area" role="img" aria-label="Faint snowflake pattern across the card"></div>
    <div class="ornament-area" role="img" aria-label="Pink floral swirl ornament"></div>
    <div class="accent-photo" role="img" aria-label="Soft faded photo of a second outfit from the style box"></div>
    <div class="model-photo" role="img" aria-label="Photo of a model in a short black dress"></div>
    <h1 class="headline"><span class="word-dark">Kite</span><span class="word-gold">Marvel</span></h1>
    <div class="gold-rule"></div>
    <p class="tagline-pill">The gift that keeps on styling</p>
  </main>
</body>
</html>
```